Accountability Project Graphics

I want to create 10 social media graphics (new Instagram size 4:5 (1080 x 1350 pixels) focusing on our Quilvo Accountability App, using any of the 3 pictures attached. Use the attached pics only, NO RANDOM STOCK PHOTOGRAPHY. For the color scheme, use the landing page colors/fonts (attached).
You can add any of the 3 photos attached but I mainly need BOLD text that includes these headlines and sub-headlines on them.
Please NOTE for all the headlines below, also add this sub-headline on each graphic:
Stay Consistent with RT in Your Pocket!
Here are the headlines:
• Stop Starting Over Every Monday
• You don't need more willpower. You need more support
• Built for women who are tired of doing this alone
• When Motivation Fades, RT Checks In
• The Support System You've Been Missing
• Support When Motivation Disappears
• What if RT Checked in Every Day?
• The Missing Piece Isn't Another Diet
• Eat the food you love. Stay accountable every day.
• One Bad Meal Doesn't Mean You Failed
women over 40 trying to lose weight

```html
<!DOCTYPE html>
<html lang="en">
<head>
<meta charset="utf-8">
<title>Quilvo Accountability Graphics</title>
<link rel="stylesheet" href="https://fonts.googleapis.com/css2?family=Playfair+Display:wght@700;800&family=Poppins:ital,wght@1,500&display=swap">
<style>
:root{
  --stage:#e6e6e6;
  --pink:#fcd0de;
  --pink-light:#fde2eb;
  --magenta:#b8275a;
  --rose:#c7577c;
  --plum:#6e2d58;
  --night:#2e1a3d;
  --white:#ffffff;
  --photo-warm:linear-gradient(160deg,#c9b7a8,#5a4a52 60%,#2b2633);
  --photo-bright:linear-gradient(160deg,#e9d6e6,#d07a8e 45%,#b9d79a 90%);
}
*{margin:0;padding:0;box-sizing:border-box}
html,body{width:1200px;height:2785px;overflow:hidden;background:var(--stage)}
.card{position:absolute;width:371px;height:463px;overflow:hidden;background:var(--pink)}
.col-a{left:222px}.col-b{left:603px}
.row-1{top:197px}.row-2{top:673px}.row-3{top:1149px}.row-4{top:1623px}.row-5{top:2098px}
.headline{position:absolute;font-family:"Playfair Display",serif;font-weight:700;color:var(--night);line-height:1.1}
.accent{color:var(--magenta)}
.center{left:0;right:0;text-align:center}
.rule{position:absolute;height:1.5px;width:38px;background:var(--magenta)}
.rule.light{background:var(--white)}
.tagline{position:absolute;font-family:"Poppins",sans-serif;font-style:italic;font-weight:500;font-size:14px;color:var(--night);line-height:1.5;letter-spacing:.2px;white-space:nowrap}
.tagline.light{color:var(--white)}
.photo{position:absolute}
.photo.warm{background:var(--photo-warm)}
.photo.bright{background:var(--photo-bright)}
.photo.person{background:linear-gradient(180deg,#3a2a33,#151520)}
.shape{position:absolute}
</style>
</head>
<body>

<!-- 1 -->
<section class="card col-a row-1">
  <div class="shape" style="left:0;top:388px;width:371px;height:75px;background:var(--night)"></div>
  <div class="photo person" role="img" aria-label="Coach in black lace top, hand on hip, smiling" style="left:216px;top:30px;width:155px;height:433px;border-radius:90px 0 0 0"></div>
  <h2 class="headline" style="left:27px;top:28px;font-size:41px;line-height:1.24;letter-spacing:-.3px"><span class="accent">Stop<br>Starting<br>Over</span><br>Every<br>Monday</h2>
  <div class="rule" style="left:27px;top:298px;width:66px"></div>
  <p class="tagline" style="left:27px;top:312px">Stay Consistent with<br>RT in Your Pocket!</p>
</section>

<!-- 2 -->
<section class="card col-b row-1">
  <h2 class="headline center" style="top:22px;font-size:33px;line-height:1.2;padding:0 12px"><span class="accent">You Don't Need More Willpower.</span> You Need More Support</h2>
  <div class="rule" style="left:151px;top:162px;width:68px"></div>
  <p class="tagline center" style="top:178px">Stay Consistent with RT in Your Pocket!</p>
  <div class="shape" style="left:28px;top:260px;width:322px;height:240px;border:8px solid var(--rose);border-radius:90px 90px 0 0"></div>
  <div class="photo bright" role="img" aria-label="Coach hugging a client, both laughing" style="left:36px;top:215px;width:306px;height:248px;border-radius:82px 82px 0 0"></div>
</section>

<!-- 3 -->
<section class="card col-a row-2">
  <div class="photo warm" role="img" aria-label="Coach and client standing together, laughing" style="inset:0"></div>
  <svg class="shape" width="371" height="463" style="left:0;top:0"><polygon points="0,70 371,463 0,463" fill="#2e1a3d" opacity=".85"/><polygon points="0,260 200,463 0,463" fill="#6e2d58" opacity=".4"/></svg>
  <h2 class="headline" style="left:12px;top:230px;font-size:34px;color:var(--white)">Built For<br>Women Who<br>Are Tired Of<br>Doing This Alone</h2>
  <div class="rule light" style="left:12px;top:405px;width:68px"></div>
  <p class="tagline light" style="left:12px;top:422px">Stay Consistent with RT in Your Pocket!</p>
</section>

<!-- 4 -->
<section class="card col-b row-2" style="background:var(--pink-light)">
  <h2 class="headline center" style="top:20px;font-size:34px;line-height:1.2"><span class="accent">When Motivation</span><br>Fades, RT Checks In</h2>
  <div class="rule" style="left:151px;top:119px;width:68px"></div>
  <p class="tagline center" style="top:136px">Stay Consistent withRT in Your Pocket!</p>
  <div class="shape" style="left:83px;top:185px;width:206px;height:278px;background:var(--rose);border-radius:103px 103px 0 0"></div>
  <div class="photo person" role="img" aria-label="Coach in black lace top, hand on hip" style="left:118px;top:180px;width:160px;height:283px;border-radius:60px 60px 0 0"></div>
</section>

<!-- 5 -->
<section class="card col-a row-3">
  <div class="photo warm" role="img" aria-label="Coach in black outfit at a bright home game room" style="inset:0"></div>
  <svg class="shape" width="371" height="463" style="left:0;top:0"><polygon points="371,35 371,463 0,463" fill="#2e1a3d" opacity=".85"/></svg>
  <h2 class="headline" style="right:22px;top:162px;font-size:34px;color:var(--white);text-align:right;line-height:1.24">The<br>Support<br>System<br>You've Been<br>Missing</h2>
  <div class="rule light" style="right:22px;top:400px;width:68px"></div>
  <p class="tagline light" style="right:22px;top:418px">Stay Consistent withRT in Your Pocket!</p>
</section>

<!-- 6 -->
<section class="card col-b row-3">
  <div class="photo bright" role="img" aria-label="Coach hugging a laughing client in a store" style="inset:0"></div>
  <svg class="shape" width="371" height="463" style="left:0;top:0"><polygon points="0,330 50,283 320,283 371,330 371,463 0,463" fill="#6e2d58"/></svg>
  <h2 class="headline center" style="top:293px;font-size:32px;line-height:1.2;color:var(--white)">Support When<br>Motivation Disappears</h2>
  <div class="rule light" style="left:151px;top:400px;width:68px"></div>
  <p class="tagline light center" style="top:418px">Stay Consistent withRT in Your Pocket!</p>
</section>

<!-- 7 -->
<section class="card col-a row-4">
  <div class="photo warm" role="img" aria-label="Coach in black outfit, smiling, hand on hip" style="inset:0"></div>
  <svg class="shape" width="371" height="463" style="left:0;top:0"><path d="M275,0 C255,20 290,40 250,60 C215,80 240,110 200,130 C150,150 125,170 128,210 C132,260 118,290 145,322 C168,352 148,382 172,410 C188,440 205,463 215,463 L371,463 L371,0 Z" fill="#c7577c" stroke="#fff" stroke-width="5"/></svg>
  <h2 class="headline" style="right:25px;top:140px;font-size:32px;color:var(--white);text-align:right;line-height:1.3">What If<br>RT Checked<br>In Every<br>Day?</h2>
  <div class="rule light" style="right:25px;top:328px;width:68px"></div>
  <p class="tagline light" style="right:25px;top:346px;text-align:right">Stay Consistent with<br>RT in Your Pocket!</p>
</section>

<!-- 8 -->
<section class="card col-b row-4" style="background:var(--white)">
  <h2 class="headline center" style="top:10px;font-size:33px;line-height:1.24"><span style="color:var(--rose)">The Missing Piece</span><br>Isn't Another Diet</h2>
  <div class="rule" style="left:151px;top:96px;width:68px"></div>
  <p class="tagline center" style="top:112px">Stay Consistent withRT in Your Pocket!</p>
  <svg class="shape" width="371" height="310" style="left:0;top:163px"><polygon points="0,110 90,25 200,0 290,20 371,100 371,310 0,310" fill="#c7577c"/><polygon points="120,10 210,0 300,40 250,20" fill="#2e1a3d"/></svg>
  <div class="photo warm" role="img" aria-label="Coach and client standing together, laughing" style="left:0;top:180px;width:371px;height:283px;clip-path:polygon(0 32%,25% 6%,55% 0,80% 8%,100% 35%,100% 100%,0 100%)"></div>
</section>

<!-- 9 -->
<section class="card col-a row-5">
  <div class="photo warm" role="img" aria-label="Coach and client standing together, laughing" style="inset:0"></div>
  <div class="shape" style="left:-40px;top:-60px;width:451px;height:270px;background:var(--rose);border-radius:0 0 50% 50%"></div>
  <div class="shape" style="left:-40px;top:-60px;width:440px;height:265px;background:var(--night);border-radius:0 0 50% 50%"></div>
  <h2 class="headline center" style="top:14px;font-size:27px;color:var(--white);line-height:1.18"><span style="color:#e4558a">Eat The Food You Love.</span><br>Stay Accountable<br>Every Day.</h2>
  <div class="rule light" style="left:166px;top:125px;background:var(--rose)"></div>
  <p class="tagline light center" style="top:134px;font-size:11.5px">Stay Consistent withRT in Your Pocket!</p>
</section>

<!-- 10 -->
<section class="card col-b row-5">
  <h2 class="headline center" style="top:14px;font-size:33px;line-height:1.2">One Bad Meal Doesn't<br>Mean You Failed</h2>
  <div class="rule" style="left:151px;top:103px;width:68px"></div>
  <p class="tagline center" style="top:120px">Stay Consistent withRT in Your Pocket!</p>
  <div class="photo" role="img" aria-label="Coach hugging a laughing client" style="left:0;top:155px;width:371px;height:308px;background:radial-gradient(ellipse at 55% 60%,#d8b27c 0%,#c43f78 45%,#e98fb3 70%,var(--pink) 100%)"></div>
</section>

</body>
</html>
```